Stationary design for new digital markerting company

I need a stationary design for a new digital marketing company called Mossy Lantern.
We work with businesses to help them create and increase their online presence in order to increase awareness of their brand.
The design must keep with the colour schemes of our logo.
I would like a design that stands out but isn't over the top while also being professional and sophisticated.

Target Market(s)

other businesses

Industry/Entity Type

Business Consultant

Font styles to use
Sans Serif

Colors
abd036
ffffff
a54499

Requirements
Must have
• logo, plus the same colour scheme

```html
<!DOCTYPE html>
<html lang="en">
<head>
<meta charset="utf-8">
<title>Mossy Lantern Stationery</title>
<link href="https://fonts.googleapis.com/css2?family=Questrial&display=swap" rel="stylesheet">
<style>
  :root {
    --magenta: #a54499;
    --magenta-dark: #9a2f8a;
    --green: #abd036;
    --white: #ffffff;
    --paper: #f7f7f7;
    --ink: #555555;
    --backdrop: #e2e2e2;
  }
  * { box-sizing: border-box; margin: 0; padding: 0; }
  html, body { width: 1200px; height: 900px; overflow: hidden; }
  body {
    background: var(--backdrop);
    font-family: "Questrial", sans-serif;
    color: var(--ink);
    position: relative;
  }
  .piece { position: absolute; overflow: hidden; }
  .piece > svg.shape { position: absolute; left: 0; top: 0; }

  .brand-name {
    position: absolute;
    color: var(--magenta);
    text-transform: uppercase;
    letter-spacing: 0.04em;
    white-space: nowrap;
    line-height: 1;
  }
  .brand-name.on-dark { color: var(--white); }
  .tagline {
    position: absolute;
    letter-spacing: 0.18em;
    white-space: nowrap;
    line-height: 1;
    color: var(--magenta);
  }
  .tagline.on-dark { color: var(--white); }

  /* Letterhead */
  .letterhead { left: 220px; top: 53px; width: 382px; height: 541px; background: var(--paper); }
  .letterhead .brand-name { left: 0; width: 382px; text-align: center; top: 63px; font-size: 16px; }
  .letterhead .tagline { left: 0; width: 382px; text-align: center; top: 82px; font-size: 5.5px; }
  .letter-body {
    position: absolute; left: 36px; top: 184px; width: 312px;
    font-size: 5.6px; line-height: 1.3; text-align: justify;
  }
  .letter-body p { margin-bottom: 6px; }
  .letter-body .salutation { font-weight: bold; color: #333; margin-bottom: 8px; }
  .sign-off { position: absolute; left: 36px; top: 347px; font-size: 5.6px; line-height: 1.4; }
  .sign-off strong { color: #333; }
  .signature-area { position: absolute; left: 100px; top: 335px; width: 70px; height: 36px; }
  .contact-row {
    position: absolute; left: 36px; top: 527px; width: 320px;
    display: flex; gap: 10px; align-items: center;
    font-size: 5.5px; color: var(--white); white-space: nowrap;
  }
  .contact-row span { display: flex; align-items: center; gap: 3px; }

  /* Folder */
  .folder { left: 649px; top: 40px; width: 416px; height: 554px; background: var(--magenta); border-radius: 3px; }
  .folder .spine { position: absolute; left: 0; top: 0; width: 27px; height: 100%; background: var(--magenta-dark); opacity: 0.35; }
  .folder .brand-name { left: 0; width: 416px; text-align: center; top: 131px; font-size: 21px; padding-left: 38px; }
  .folder .tagline { left: 0; width: 416px; text-align: center; top: 151px; font-size: 7.5px; padding-left: 38px; }

  /* Business cards */
  .card-front { left: 78px; top: 638px; width: 164px; height: 91px; background: var(--paper); }
  .card-front .holder { position: absolute; left: 10px; top: 20px; font-size: 5.5px; line-height: 1.3; }
  .card-front .holder strong { color: #222; font-size: 5.8px; }
  .card-front .details { position: absolute; left: 10px; top: 42px; font-size: 4.2px; line-height: 1.45; }
  .card-front .details span { display: flex; align-items: center; gap: 2px; }
  .card-front .details .address { margin-top: 3px; }
  .card-front .brand-name { left: 72px; top: 47px; font-size: 9.5px; }
  .card-front .tagline { left: 77px; top: 58px; font-size: 3.4px; }
  .card-back { left: 78px; top: 748px; width: 164px; height: 91px; background: var(--magenta); }
  .card-back .brand-name { left: 0; width: 164px; text-align: center; top: 51px; font-size: 10px; }
  .card-back .tagline { left: 0; width: 164px; text-align: center; top: 63px; font-size: 3.4px; }

  /* Envelope front */
  .envelope-front { left: 278px; top: 639px; width: 400px; height: 200px; background: var(--paper); }
  .envelope-front .brand-name { left: 27px; top: 61px; font-size: 13.5px; }
  .envelope-front .tagline { left: 31px; top: 76px; font-size: 5px; }
  .envelope-front .return-address { position: absolute; left: 22px; top: 185px; font-size: 5.5px; color: var(--white); }

  /* Envelope back */
  .envelope-back { left: 724px; top: 639px; width: 400px; height: 200px; background: var(--paper); }
</style>
</head>
<body>

<section class="piece letterhead" aria-label="Letterhead">
  <svg class="shape" width="382" height="541" viewBox="0 0 382 541">
    <path d="M0 0 H382 V44 Q191 8 0 44 Z" fill="var(--magenta)"/>
    <path d="M0 46 Q191 10 382 46" fill="none" stroke="var(--green)" stroke-width="3"/>
    <circle cx="191" cy="33" r="24" fill="var(--white)"/>
    <circle cx="191" cy="33" r="19" fill="var(--green)"/>
    <path d="M0 506 Q191 528 382 506" fill="none" stroke="var(--green)" stroke-width="3"/>
    <path d="M0 510 Q191 532 382 510 V541 H0 Z" fill="var(--magenta)"/>
  </svg>
  <div class="brand-name">Mossy Lantern</div>
  <div class="tagline">Lighting Up the Page Ranks</div>

  <div class="letter-body">
    <p class="salutation">Dear sir,</p>
    <p>Good communication sits at the heart of every working relationship. A clear message builds trust, sets expectations and keeps projects moving forward. We believe that a thoughtful letter still carries weight in a busy digital world, and we take care with every one we send.</p>
    <p>Our team helps businesses grow their online presence through search, content and social campaigns that suit their audience. We study how customers look for services, then shape pages and posts so that the right people find them. Each plan is built around measurable goals, and we report on progress every month so that you always know where things stand and what comes next.</p>
    <p>We would welcome the chance to discuss your goals in person. A short meeting is often enough to find the quick wins that make a real difference to your brand.</p>
    <p>Thank you for your time. We look forward to hearing from you and to helping your business shine online.</p>
  </div>
  <div class="sign-off">Yours Sincerely,<br><strong>Owen Harlow</strong></div>
  <div class="signature-area" role="img" aria-label="Handwritten signature" style="background: linear-gradient(90deg, rgba(70,100,190,0) 0%, rgba(70,100,190,0.18) 50%, rgba(70,100,190,0) 100%);"></div>

  <div class="contact-row">
    <span>Level 12, Fern House, 8 Quarry Lane, Ashford</span>
    <span><svg width="6" height="6" viewBox="0 0 10 10"><rect width="10" height="10" rx="1.5" fill="var(--white)"/><path d="M3 2.5 L4.3 2.5 L4.8 4 L4 4.6 Q4.8 6 6 6.2 L6.6 5.4 L8 6 V7.5 Q5.5 7.8 3.8 6 Q2.4 4.4 3 2.5Z" fill="var(--magenta)"/></svg>1300 555 018</span>
    <span><svg width="6" height="6" viewBox="0 0 10 10"><rect width="10" height="10" rx="1.5" fill="var(--white)"/><rect x="2" y="3" width="6" height="4" fill="none" stroke="var(--magenta)" stroke-width="0.9"/><path d="M2 3 L5 5.5 L8 3" fill="none" stroke="var(--magenta)" stroke-width="0.9"/></svg>hello@mossylantern.com</span>
    <span><svg width="6" height="6" viewBox="0 0 10 10"><rect width="10" height="10" rx="1.5" fill="var(--white)"/><circle cx="5" cy="5" r="3" fill="none" stroke="var(--magenta)" stroke-width="0.9"/><path d="M2 5 H8 M5 2 V8" stroke="var(--magenta)" stroke-width="0.7"/></svg>www.mossylantern.com</span>
  </div>
</section>

<section class="piece folder" aria-label="Presentation folder">
  <div class="spine"></div>
  <svg class="shape" width="416" height="554" viewBox="0 0 416 554">
    <circle cx="227" cy="96" r="26" fill="var(--green)"/>
  </svg>
  <div class="brand-name on-dark">Mossy Lantern</div>
  <div class="tagline on-dark">Lighting Up the Page Ranks</div>
</section>

<section class="piece card-front" aria-label="Business card front">
  <svg class="shape" width="164" height="91" viewBox="0 0 164 91">
    <path d="M0 0 H164 V14 Q82 2 0 14 Z" fill="var(--magenta)"/>
    <path d="M0 15 Q82 3 164 15" fill="none" stroke="var(--green)" stroke-width="1.5"/>
    <circle cx="115" cy="27" r="14" fill="var(--white)"/>
    <circle cx="115" cy="27" r="11" fill="var(--green)"/>
    <path d="M0 81 Q82 90 164 81" fill="none" stroke="var(--green)" stroke-width="1.5"/>
    <path d="M0 83 Q82 92 164 83 V91 H0 Z" fill="var(--magenta)"/>
  </svg>
  <div class="holder"><strong>CLARA WENDELL</strong><br>Managing Director</div>
  <div class="details">
    <span><svg width="4" height="4" viewBox="0 0 4 4"><rect width="4" height="4" fill="var(--green)"/></svg>1300 555 018</span>
    <span><svg width="4" height="4" viewBox="0 0 4 4"><rect width="4" height="4" fill="var(--green)"/></svg>hello@mossylantern.com</span>
    <span><svg width="4" height="4" viewBox="0 0 4 4"><rect width="4" height="4" fill="var(--green)"/></svg>www.mossylantern.com</span>
    <div class="address">Level 12, Fern House<br>8 Quarry Lane, Ashford</div>
  </div>
  <div class="brand-name">Mossy Lantern</div>
  <div class="tagline">Lighting Up the Page Ranks</div>
</section>

<section class="piece card-back" aria-label="Business card back">
  <svg class="shape" width="164" height="91" viewBox="0 0 164 91">
    <circle cx="82" cy="37" r="12" fill="var(--green)"/>
  </svg>
  <div class="brand-name on-dark">Mossy Lantern</div>
  <div class="tagline on-dark">Lighting Up the Page Ranks</div>
</section>

<section class="piece envelope-front" aria-label="Envelope front">
  <svg class="shape" width="400" height="200" viewBox="0 0 400 200">
    <path d="M0 0 H400 V30 Q200 2 0 30 Z" fill="var(--magenta)"/>
    <path d="M0 32 Q200 4 400 32" fill="none" stroke="var(--green)" stroke-width="2.5"/>
    <circle cx="78" cy="36" r="21" fill="var(--white)"/>
    <circle cx="78" cy="36" r="17" fill="var(--green)"/>
    <path d="M0 168 Q200 186 400 168" fill="none" stroke="var(--green)" stroke-width="2.5"/>
    <path d="M0 172 Q200 190 400 172 V200 H0 Z" fill="var(--magenta)"/>
  </svg>
  <div class="brand-name">Mossy Lantern</div>
  <div class="tagline">Lighting Up the Page Ranks</div>
  <div class="return-address">Level 12, Fern House, 8 Quarry Lane, Ashford</div>
</section>

<section class="piece envelope-back" aria-label="Envelope back">
  <svg class="shape" width="400" height="200" viewBox="0 0 400 200">
    <path d="M0 0 H400 L385 56 H15 Z" fill="var(--magenta)"/>
    <circle cx="200" cy="27" r="8.5" fill="var(--green)"/>
  </svg>
</section>

</body>
</html>
```